Computer Training in the Education sector - Letterhead

We need a new letter head to be designed for the company. We provide computer training fro the Education Sector, both primary and private tertiary providers. The colours will need to tie in with the website www.crossingthestream.co.nz.
The company name is Crossing the Stream with the tag line of Computer Training for Educators.
The footer will need to have the following detail...
0508 PCS MENTOR
021 839 415
www.crossingthestream.co.nz / training@crossingthestream.co.nz
Updates

Thanks for the designs so far.

Some have watermarks in the background. Please don't worry about using watermarks as I will not be using a watermark in in a final design.
Regards,
Roger

Thank you for all the designs and the effort. There was some great concepts that came through.

Cheers
Roger

Industry/Entity Type

Computer

```html
<!DOCTYPE html>
<html lang="en">
<head>
<meta charset="utf-8">
<title>Crossing the Stream – Letterhead</title>
<link rel="stylesheet" href="https://fonts.googleapis.com/css2?family=Roboto:wght@400&display=swap">
<style>
  :root {
    --brand-blue: #2e74b8;
    --brand-orange: #e5822f;
    --brand-green: #7cb342;
    --ink: #1e1e1e;
    --ink-soft: #3a3a3a;
    --paper: #ffffff;
  }
  * { margin: 0; padding: 0; box-sizing: border-box; }
  html, body { width: 1034px; height: 1200px; overflow: hidden; background: var(--paper); }
  .letterhead {
    position: relative;
    width: 1034px;
    height: 1200px;
    background: var(--paper);
    font-family: "Roboto", Arial, sans-serif;
    color: var(--ink);
  }
  .header-band { position: absolute; top: 0; left: 0; width: 1034px; height: 170px; }
  .brand-name {
    position: absolute;
    top: 82px;
    left: 0;
    width: 1034px;
    text-align: center;
    font-size: 40px;
    line-height: 46px;
    font-weight: 400;
    color: var(--brand-blue);
  }
  .contact-bar {
    position: absolute;
    left: 0; top: 1081px;
    width: 10px; height: 90px;
    background: var(--brand-blue);
    border-radius: 0 5px 5px 0;
  }
  .contact-list {
    position: absolute;
    left: 34px; top: 1082px;
    list-style: none;
    font-size: 16px;
    color: var(--ink-soft);
  }
  .contact-list li { display: flex; align-items: center; height: 22.5px; }
  .contact-list svg { width: 13px; height: 13px; margin-right: 8px; flex: none; }
  .tagline {
    position: absolute;
    right: 23px; top: 1100px;
    text-align: right;
    font-size: 21px;
    line-height: 26px;
    letter-spacing: 1.3px;
    color: var(--ink);
  }
  .tagline-bar {
    position: absolute;
    right: 0; top: 1095px;
    width: 7px; height: 62px;
    background: var(--brand-orange);
    border-radius: 4px 0 0 4px;
  }
</style>
</head>
<body>
<main class="letterhead">
  <svg class="header-band" viewBox="0 0 1034 170" aria-hidden="true">
    <path d="M0 0 H1034 V126 Q517 -72 0 126 Z" fill="var(--brand-blue)"/>
    <path d="M0 158 Q517 -89 1034 158" fill="none" stroke="var(--brand-orange)" stroke-width="9"/>
  </svg>

  <h1 class="brand-name">Crossing<br>the Stream</h1>

  <div class="contact-bar"></div>
  <ul class="contact-list">
    <li>
      <svg viewBox="0 0 14 14"><circle cx="7" cy="7" r="6" fill="none" stroke="var(--brand-green)" stroke-width="1.4"/><path d="M5 4 Q4 8 8 10" fill="none" stroke="var(--brand-green)" stroke-width="1.8" stroke-linecap="round"/></svg>
      0508 PCS MENTOR
    </li>
    <li>
      <svg viewBox="0 0 14 14"><circle cx="7" cy="7" r="6" fill="none" stroke="var(--brand-green)" stroke-width="1.4"/><path d="M5 4 Q4 8 8 10" fill="none" stroke="var(--brand-green)" stroke-width="1.8" stroke-linecap="round"/></svg>
      021 839 415
    </li>
    <li>
      <svg viewBox="0 0 14 14"><path d="M1 5 L7 1.5 L13 5 V12 H1 Z" fill="var(--brand-green)"/><path d="M1 5 L7 9 L13 5" fill="none" stroke="#fff" stroke-width="1.2"/></svg>
      training@crossingthestream.co.nz
    </li>
    <li>
      <svg viewBox="0 0 14 14" fill="none" stroke="var(--brand-green)" stroke-width="1.2"><circle cx="7" cy="7" r="6"/><ellipse cx="7" cy="7" rx="2.6" ry="6"/><path d="M1 7 H13 M2 4 H12 M2 10 H12"/></svg>
      www.crossingthestream.co.nz
    </li>
  </ul>

  <p class="tagline">Computer Training<br>for Educators</p>
  <div class="tagline-bar"></div>
</main>
</body>
</html>
```